Business Card Design - Amberfield Court

We are looking at a new design for our business cards that has a modern and professional look. We run a residential aged care facility focussing on the care of residents. The cards will be used for potential clients, consultants and business opportunities in this sector. Blue and white is our main colours and would to see these colours incorporated in the design.
Industry/Entity Type
Business
Contact Information for Business Card
Amberfield Court, Darren Walsh, dwalsh@amberfieldcourt.com.au, Finance Manager, 0472 639 208, BCom, 37 Marrabel Crescent, Brindle Vale, Qld 4093.
Look and feel
Each slider illustrates characteristics of the customer's brand and the style your logo design should communicate.

```html
<!DOCTYPE html>
<html lang="en">
<head>
<meta charset="utf-8">
<title>Amberfield Court – Business Card</title>
<link rel="stylesheet" href="https://fonts.googleapis.com/css2?family=Open+Sans:wght@600;700&family=Arimo:wght@400&display=swap">
<style>
  :root {
    --backdrop: #e9e7e3;
    --card-white: #ffffff;
    --brand-blue: #43738f;
    --brand-blue-light: #5283a0;
    --brand-blue-dark: #3a6681;
    --warm-grey: #a59c98;
    --text-grey: #555555;
    --divider: #c9c9c9;
  }
  * { box-sizing: border-box; margin: 0; padding: 0; }
  html, body {
    width: 1200px;
    height: 950px;
    overflow: hidden;
    background: var(--backdrop);
  }
  .card {
    position: absolute;
    left: 220px;
    width: 760px;
    height: 435px;
    overflow: hidden;
    box-shadow: 0 8px 24px rgba(0,0,0,0.18);
  }

  /* Back side */
  .card-back {
    top: 28px;
    background: linear-gradient(135deg, var(--brand-blue-dark) 0%, var(--brand-blue) 55%, var(--brand-blue-light) 100%);
  }
  .back-lockup {
    position: absolute;
    inset: 0;
    display: flex;
    align-items: center;
    justify-content: center;
    gap: 18px;
  }
  .back-dot {
    width: 52px;
    height: 52px;
    border-radius: 50%;
    background: var(--card-white);
    flex: none;
  }
  .back-name {
    font-family: "Arimo", Arial, sans-serif;
    font-weight: 400;
    font-size: 40px;
    color: var(--card-white);
  }

  /* Front side */
  .card-front {
    top: 487px;
    background: var(--card-white);
  }
  .card-waves {
    position: absolute;
    inset: 0;
    width: 100%;
    height: 100%;
  }
  .brand-lockup {
    position: absolute;
    left: 40px;
    top: 120px;
    display: flex;
    align-items: center;
    gap: 12px;
  }
  .brand-dot {
    width: 34px;
    height: 34px;
    border-radius: 50%;
    background: var(--brand-blue);
    flex: none;
  }
  .brand-name {
    font-family: "Arimo", Arial, sans-serif;
    font-weight: 400;
    font-size: 24px;
    color: var(--brand-blue);
    white-space: nowrap;
  }
  .card-divider {
    position: absolute;
    left: 302px;
    top: 78px;
    width: 1px;
    height: 180px;
    background: var(--divider);
  }
  .contact-block {
    position: absolute;
    left: 325px;
    top: 74px;
    font-family: "Arimo", Arial, sans-serif;
    color: var(--text-grey);
  }
  .person-name {
    font-family: "Open Sans", Arial, sans-serif;
    font-weight: 700;
    font-size: 23px;
    color: var(--brand-blue);
    line-height: 1.15;
  }
  .person-name .credential {
    font-weight: 600;
    font-size: 17px;
  }
  .person-role {
    font-size: 17px;
    color: var(--warm-grey);
    margin-bottom: 12px;
  }
  .postal-address {
    font-style: normal;
    font-size: 18px;
    line-height: 1.3;
    margin-bottom: 8px;
  }
  .contact-list { list-style: none; }
  .contact-item {
    display: flex;
    align-items: center;
    gap: 10px;
    font-size: 18px;
    line-height: 1.4;
    white-space: nowrap;
  }
  .contact-icon {
    width: 16px;
    height: 16px;
    flex: none;
    fill: var(--text-grey);
  }
</style>
</head>
<body>
  <article class="card card-back">
    <div class="back-lockup">
      <span class="back-dot"></span>
      <span class="back-name">Amberfield Court</span>
    </div>
  </article>

  <article class="card card-front">
    <svg class="card-waves" viewBox="0 0 760 435" preserveAspectRatio="none" aria-hidden="true">
      <path d="M0,298 C170,336 400,380 760,384" fill="none" stroke="var(--warm-grey)" stroke-width="7"/>
      <path d="M0,314 C160,352 390,396 760,398 L760,435 L0,435 Z" fill="var(--brand-blue)"/>
    </svg>

    <div class="brand-lockup">
      <span class="brand-dot"></span>
      <span class="brand-name">Amberfield Court</span>
    </div>

    <div class="card-divider"></div>

    <section class="contact-block">
      <h1 class="person-name">Darren Walsh <span class="credential">BCom</span></h1>
      <p class="person-role">Finance Manager</p>
      <address class="postal-address">37 Marrabel Crescent<br>Brindle Vale, Qld 4093.</address>
      <ul class="contact-list">
        <li class="contact-item">
          <svg class="contact-icon" viewBox="0 0 24 24"><path d="M6.6 10.8a15 15 0 0 0 6.6 6.6l2.2-2.2a1 1 0 0 1 1-.25 11.4 11.4 0 0 0 3.6.57 1 1 0 0 1 1 1V20a1 1 0 0 1-1 1A17 17 0 0 1 3 4a1 1 0 0 1 1-1h3.5a1 1 0 0 1 1 1c0 1.25.2 2.45.57 3.57a1 1 0 0 1-.25 1Z"/></svg>
          0472 639 208
        </li>
        <li class="contact-item">
          <svg class="contact-icon" viewBox="0 0 24 24"><path d="M2 5h20v14H2Zm2 2v.5l8 5 8-5V7l-8 5Z"/></svg>
          dwalsh@amberfieldcourt.com.au
        </li>
        <li class="contact-item">
          <svg class="contact-icon" viewBox="0 0 24 24"><circle cx="12" cy="12" r="10"/><path d="M9 8l7 4-7 4Z" fill="#fff"/></svg>
          www.amberfieldcourt.com.au
        </li>
      </ul>
    </section>
  </article>
</body>
</html>
```